Pine Ledge Traders, LLC- Global Beverage Company with 100% Cold Chain Logistics

Hey All, My Name is Dale, I am a young business owner in a competitive export space, but my niche is that I am shipping all of my beer around the world, "100% Cold Chain". This model is more costly, but it protects the integrity of the beer itself and will give folks in foreign countries the best representation of what US Craft Beer has to offer.

I am not a branding guy and don't claim to be one, I am a salesperson first, and will be referring to all of you to create something great that will be memorable.

I am looking for a basic Business Card Design for my Craft Beer Export company. I sell US Craft Beer in several countries around the globe. Austrailia, China, Taiwan, Chile, France, New Zealand... to name a few.

I am looking for a sleek, modern, and fresh design. Quickly!

Thanks for your consideration!

Cheers,

Dale

Target Market(s)

International

Contact Information for Business Card

Dale Corrigan
Founder- Roaming Hops Guy
Dale@PineLedgeTraders.example
@RoamingHopsGuy- Instagram only
www.Pineledgetraders.example
@PineLedgeTradersAU- Instagram Only

Font styles to use
Serif

Colors
0592cd
ffffff

Requirements
Must have
• Name-
• Title-
• Email-
• Social Media Handle-
• Company Website-
Nice to have
• Nice Logo/ Images on Card
Should not have
• Tacky Beer Images

```html
<!DOCTYPE html>
<html lang="en">
<head>
<meta charset="utf-8">
<title>Pine Ledge Traders – Business Card</title>
<link href="https://fonts.googleapis.com/css2?family=Montserrat:wght@700;800&family=Roboto:wght@300;400&display=swap" rel="stylesheet">
<style>
  :root {
    --brand-blue: #0592cd;
    --white: #ffffff;
    --card-white: #f1f1f1;
    --ink: #444444;
    --rule: #9a9a9a;
    --backdrop: #1b1b1b;
  }
  * { box-sizing: border-box; margin: 0; padding: 0; }
  html, body {
    width: 1200px; height: 900px; overflow: hidden;
    background: var(--backdrop);
  }
  .stage {
    width: 1200px; height: 900px;
    display: flex; align-items: center; justify-content: center; gap: 40px;
  }
  .card {
    position: relative;
    width: 540px; height: 310px;
    border-radius: 26px;
    overflow: hidden;
  }
  /* Front */
  .card-front {
    background: var(--brand-blue);
    color: var(--white);
  }
  .front-name {
    position: absolute; left: 48px; top: 88px;
    font-family: 'Montserrat', sans-serif; font-weight: 800;
    font-size: 40px; line-height: 0.98; letter-spacing: 0.5px;
    text-transform: uppercase;
  }
  .front-tagline {
    position: absolute; left: 50px; top: 196px;
    font-family: 'Roboto', sans-serif; font-weight: 400; font-size: 19px;
  }
  .front-countries {
    position: absolute; left: 50px; bottom: 26px;
    font-family: 'Roboto', sans-serif; font-weight: 300; font-size: 12px;
    color: rgba(255,255,255,0.72); letter-spacing: 0.3px;
  }
  /* Back */
  .card-back {
    background: var(--card-white);
    color: var(--ink);
    font-family: 'Roboto', sans-serif;
  }
  .brand-lockup {
    position: absolute; top: 46px; left: 0; right: 0;
    display: flex; align-items: center; justify-content: center; gap: 14px;
  }
  .brand-mark {
    width: 38px; height: 38px; border-radius: 6px;
    background: var(--brand-blue);
  }
  .brand-name {
    font-family: 'Montserrat', sans-serif; font-weight: 800;
    font-size: 22px; line-height: 1; color: var(--brand-blue);
    text-transform: uppercase;
  }
  .brand-rule {
    position: absolute; left: 60px; right: 60px; top: 112px;
    height: 1px; background: var(--rule);
  }
  .person {
    position: absolute; left: 40px; bottom: 48px;
  }
  .person-name {
    font-family: 'Montserrat', sans-serif; font-weight: 700;
    font-size: 22px; color: var(--brand-blue);
  }
  .person-title { font-size: 15px; margin-top: 2px; }
  .contact {
    position: absolute; right: 34px; top: 138px;
    text-align: right; font-size: 14px; line-height: 1.35;
  }
  .contact-row { display: flex; align-items: center; justify-content: flex-end; gap: 8px; }
  .contact-gap { height: 44px; }
  .icon-square { width: 14px; height: 14px; border-radius: 2px; background: var(--brand-blue); }
  .icon-circle { width: 14px; height: 14px; border-radius: 50%; background: var(--brand-blue); }
</style>
</head>
<body>
<main class="stage">
  <section class="card card-front">
    <h1 class="front-name">Pine Ledge<br>Traders</h1>
    <p class="front-tagline">100% Cold Chain Logistics</p>
    <p class="front-countries">Austrailia | China | Taiwan | Chile | France | New Zealand</p>
  </section>

  <section class="card card-back">
    <div class="brand-lockup">
      <span class="brand-mark"></span>
      <span class="brand-name">Pine Ledge<br>Traders</span>
    </div>
    <div class="brand-rule"></div>

    <div class="person">
      <p class="person-name">Dale Corrigan</p>
      <p class="person-title">Founder - Roaming Hops Guy</p>
    </div>

    <div class="contact">
      <p class="contact-row">@RoamingHopsGuy <span class="icon-square"></span></p>
      <p class="contact-row">Dale@PineLedgeTraders.example
        <svg width="14" height="11" viewBox="0 0 14 11" aria-hidden="true">
          <rect width="14" height="11" rx="1.5" fill="#0592cd"/>
          <path d="M1.5 2 L7 6.5 L12.5 2" stroke="#fff" stroke-width="1.3" fill="none"/>
        </svg>
      </p>
      <p class="contact-row">www.Pineledgetraders.example <span class="icon-circle"></span></p>
    </div>
  </section>
</main>
</body>
</html>
```